Harbourline wall and floor tiling

I would like you to design me a wrap for my work van, I will provide the logo I would like you to work off.
I’m happy for some slight little changes.
just need some creativity with the wrap design & background.
We are a tiling business in the construction industry.
Any designs are welcome but I do like what I have going on here and this type of font.
Show me what you got.
I would like the van to have a half wrap not just the side stickers like it shows in the photos.
The new mobile numbers I would like on the wrap are
0491358027
0412864093
We cover Tiling, screeding , waterproofing

Industry/Entity Type

Construction

Colors

Designer to choose colors to be used in the design.

Requirements
Must have
• Facebook & instagram logo somewhere small. Tiling, Waterproofing & Screeding

```html
<!DOCTYPE html>
<html lang="en">
<head>
<meta charset="utf-8">
<title>Harbourline Wall &amp; Floor Tiling – Rear Van Wrap</title>
<link rel="stylesheet" href="https://fonts.googleapis.com/css2?family=Montserrat:wght@600;700&family=Bebas+Neue&display=swap">
<style>
  :root {
    --wrap-blue: #0a7fd0;
    --brand-blue: #1e96e0;
    --band-grey: #9b9b9b;
    --accent-grey: #b5b5b5;
    --panel-white: #f4f4f4;
    --page: #ffffff;
    --ink-white: #ffffff;
  }
  * { margin: 0; padding: 0; box-sizing: border-box; }
  html, body { width: 1200px; height: 1200px; overflow: hidden; background: var(--page); }
  .canvas { position: relative; width: 1200px; height: 1200px; }
  .wrap-shape { position: absolute; inset: 0; }

  .brand {
    position: absolute; left: 0; width: 1200px; top: 340px;
    display: flex; flex-direction: column; align-items: center;
  }
  .brand-mark {
    width: 34px; height: 34px; background: var(--brand-blue);
    transform: rotate(45deg); margin-bottom: 38px;
  }
  .brand-name {
    font-family: "Montserrat", sans-serif; font-weight: 700;
    color: var(--brand-blue); text-align: center; line-height: 1.05;
  }
  .brand-name .line-main { display: block; font-size: 72px; letter-spacing: 2px; }
  .brand-name .line-sub { display: block; font-size: 26px; letter-spacing: 1px; margin-top: 8px; }

  .contact { position: absolute; left: 286px; top: 716px; }
  .phone-icon { position: absolute; left: 0; top: 14px; width: 36px; height: 36px; }
  .phone-numbers {
    margin-left: 46px;
    font-family: "Montserrat", sans-serif; font-weight: 600;
    font-size: 33px; line-height: 31px; color: var(--ink-white); letter-spacing: 0.5px;
  }
  .social {
    position: absolute; left: 310px; top: 795px;
    display: flex; align-items: center; gap: 8px;
    font-family: "Bebas Neue", sans-serif; font-size: 19px; color: var(--ink-white); letter-spacing: 0.3px;
  }
  .social-square { width: 18px; height: 18px; border: 2px solid var(--ink-white); border-radius: 4px; }

  .services { position: absolute; left: 692px; top: 710px; list-style: none; }
  .services li {
    display: flex; align-items: center; gap: 14px; height: 39.5px;
    font-family: "Bebas Neue", sans-serif; font-size: 34px; color: var(--ink-white); letter-spacing: 0.5px;
  }
  .services li::before {
    content: ""; width: 13px; height: 13px; background: var(--accent-grey); transform: rotate(45deg);
  }
</style>
</head>
<body>
<main class="canvas">
  <svg class="wrap-shape" width="1200" height="1200" viewBox="0 0 1200 1200" aria-hidden="true">
    <rect class="panel-top" x="216" y="206" width="772" height="400" rx="26" fill="var(--panel-white)"/>
    <polygon class="chevron-band" points="260,580 600,534 940,580 940,592 600,550 260,598" fill="var(--band-grey)"/>
    <path class="panel-wrap" d="M216,606 L260,606 L600,559 L940,606 L988,606 L988,866 L216,866 Z" fill="var(--wrap-blue)"/>
  </svg>

  <header class="brand">
    <div class="brand-mark"></div>
    <h1 class="brand-name">
      <span class="line-main">HARBOURLINE</span>
      <span class="line-sub">WALL &amp; FLOOR TILING</span>
    </h1>
  </header>

  <section class="contact">
    <svg class="phone-icon" viewBox="0 0 36 36" aria-hidden="true">
      <circle cx="18" cy="18" r="18" fill="var(--accent-grey)"/>
      <path d="M12.5 9.5c1-.6 2 .1 2.6 1.2l1.3 2.5c.4.9.1 1.8-.6 2.3l-1 .7c.8 2 2.3 3.6 4.4 4.6l.8-1c.6-.7 1.5-.9 2.3-.5l2.5 1.3c1 .6 1.6 1.6 1 2.6-1.1 2-3 3.2-5.4 2.2-4.6-1.9-8.1-5.5-9.7-10-.7-2.1.2-4.6 1.8-5.9z" fill="var(--ink-white)"/>
    </svg>
    <p class="phone-numbers">0491 358 027<br>0412 864 093</p>
  </section>

  <p class="social"><span class="social-square"></span>@HARBOURLINEWALLANDFLOORTILING</p>

  <ul class="services">
    <li>Tiling</li>
    <li>Waterproofing</li>
    <li>Screeding</li>
  </ul>
</main>
</body>
</html>
```